Health and wellnes company needs business cards

We are a Health and wellness business just relocated to Spain. Here nobody knows our business so we would like to put some of our services on the card. Clean design with logo.

Contact Information for Business Card

Brightmeadow
Paula & Oskar Dunbeck
Calle del Almendro 57
Puerto Almendral
Mobile: 0046 731 402687
info@brightmeadow.example

Font styles to use
Serif

Colors
85cae6
85acd3
b768aa

Requirements
Must have
• these Services somewhere on the card
• - Private or group yoga
• - Reconnective healing
• - Kitesurfing lessons
• - Massage
• LOgo somewhere
Nice to have
• Colours that go with the logo please

```html
<!DOCTYPE html>
<html lang="en">
<head>
<meta charset="utf-8">
<title>Brightmeadow business cards</title>
<link rel="stylesheet" href="https://fonts.googleapis.com/css2?family=Merriweather:wght@400;700&family=Mulish:wght@400;500&display=swap">
<style>
  :root {
    --navy: #1b365f;
    --teal: #6cc3c6;
    --teal-pale: #e6f4f5;
    --paper: #ffffff;
    --ink-grey: #5a5f66;
    --rule: #c9cdd2;
    --stage: #e9ebee;
  }
  * { box-sizing: border-box; margin: 0; padding: 0; }
  html, body { width: 1200px; height: 912px; overflow: hidden; }
  body {
    background: var(--stage);
    display: flex;
    flex-direction: column;
    align-items: center;
    justify-content: center;
    gap: 30px;
    font-family: "Mulish", Arial, sans-serif;
  }
  .card {
    position: relative;
    width: 720px;
    height: 411px;
    border-radius: 22px;
    overflow: hidden;
    box-shadow: 0 6px 18px rgba(20, 30, 50, 0.18);
  }

  /* Front: wordmark and services */
  .card-front { background: var(--paper); }
  .front-brand {
    position: absolute;
    left: 150px;
    top: 50%;
    transform: translateY(-50%);
    display: flex;
    align-items: center;
    gap: 12px;
  }
  .brand-dot {
    width: 22px; height: 22px;
    border-radius: 50%;
    background: var(--teal);
  }
  .wordmark {
    font-family: "Merriweather", Georgia, serif;
    font-weight: 700;
    color: var(--navy);
    letter-spacing: 0.04em;
  }
  .front-brand .wordmark { font-size: 22px; }
  .front-divider {
    position: absolute;
    left: 386px;
    top: 128px;
    width: 1px;
    height: 155px;
    background: var(--rule);
  }
  .services {
    position: absolute;
    left: 412px;
    top: 50%;
    transform: translateY(-50%);
    list-style: none;
    color: var(--ink-grey);
    font-size: 17px;
    line-height: 1.45;
  }
  .services li { display: flex; align-items: center; gap: 10px; }
  .services li::before {
    content: "";
    width: 6px; height: 6px;
    border-radius: 50%;
    background: var(--teal);
  }

  /* Back: contact details and emblem circle */
  .card-back { background: var(--navy); }
  .back-art { position: absolute; inset: 0; }
  .emblem-name {
    position: absolute;
    left: 520px;
    top: 200px;
    transform: translate(-50%, -50%);
    font-size: 21px;
    text-transform: uppercase;
    white-space: nowrap;
  }
  .contact {
    position: absolute;
    left: 54px;
    top: 128px;
    color: var(--paper);
  }
  .contact-name {
    font-family: "Merriweather", Georgia, serif;
    font-weight: 700;
    font-size: 20px;
    margin-bottom: 22px;
  }
  .contact-address {
    font-style: normal;
    font-size: 17px;
    line-height: 1.3;
    margin-left: 34px;
    margin-bottom: 18px;
  }
  .contact-lines { list-style: none; margin-left: 34px; font-size: 17px; line-height: 1.3; }
  .contact-lines li { display: flex; align-items: center; gap: 10px; }
  .contact-lines svg { width: 15px; height: 15px; flex: none; }
</style>
</head>
<body>

  <section class="card card-front" aria-label="Card front">
    <div class="front-brand">
      <span class="brand-dot"></span>
      <span class="wordmark">Brightmeadow</span>
    </div>
    <div class="front-divider"></div>
    <ul class="services">
      <li>Private or group yoga</li>
      <li>Reconnective healing</li>
      <li>Kitesurfing lessons</li>
      <li>Massage</li>
    </ul>
  </section>

  <section class="card card-back" aria-label="Card back">
    <svg class="back-art" viewBox="0 0 720 411" aria-hidden="true">
      <path d="M380 0 H720 V330 Q560 250 380 0 Z" fill="var(--teal)"/>
      <circle cx="520" cy="200" r="176" fill="none" stroke="#ffffff" stroke-width="2"/>
      <circle cx="520" cy="200" r="164" fill="var(--teal)"/>
      <circle cx="520" cy="200" r="152" fill="var(--teal-pale)"/>
      <circle cx="520" cy="200" r="126" fill="#ffffff"/>
    </svg>
    <span class="wordmark emblem-name">Brightmeadow</span>

    <div class="contact">
      <p class="contact-name">Paula &amp; Oskar Dunbeck</p>
      <address class="contact-address">
        Calle del Almendro 57<br>
        Puerto<br>
        Almendral
      </address>
      <ul class="contact-lines">
        <li>
          <svg viewBox="0 0 16 16"><rect x="4" y="1" width="8" height="14" rx="1.5" fill="none" stroke="#fff" stroke-width="1.6"/><circle cx="8" cy="12.3" r="0.9" fill="#fff"/></svg>
          0046 731 402687
        </li>
        <li>
          <svg viewBox="0 0 16 16"><rect x="1" y="3.5" width="14" height="9" fill="#fff"/><path d="M1 3.5 L8 9 L15 3.5" fill="none" stroke="var(--navy)" stroke-width="1.2"/></svg>
          info@brightmeadow.example
        </li>
        <li>
          <svg viewBox="0 0 16 16"><circle cx="8" cy="8" r="7" fill="#fff"/><path d="M1 8 H15 M8 1 C4.5 4.5 4.5 11.5 8 15 M8 1 C11.5 4.5 11.5 11.5 8 15" fill="none" stroke="var(--navy)" stroke-width="1"/></svg>
          www.brightmeadow.example
        </li>
      </ul>
    </div>
  </section>

</body>
</html>
```